Business card for my new company (Accounting firm)

I need a business card for my new business Brightwell Advisory and Ledger SA. Our services are accounting, tax, audit and financial management. Our customers are small companies, start-ups and new companies. The final design has to show financial security, trust and growth. Please find our logo attached to the business card. Text for the business card: Brightwell Advisory and Ledger SA Tomas Varenholt Director and Founder Certified Accountant Tel. 022 418 57 34 tv@clairevalconseil.ch www.clairevalconseil.ch Rue des Vergières 27 1201 Geneva
Target Market(s)
Our customers are small companies, start-ups and new companies.
Industry/Entity Type
Finance And Accounting
Contact Information for Business Card
Claireval Conseil et Comptes SA
Tomas Varenholt
Directeur et Fondateur
Expert-comptable diplômé
Tél. 022 418 57 34
tv@clairevalconseil.ch
www.clairevalconseil.ch
Rue des Vergières 27
1201 Genève

```html
<!DOCTYPE html>
<html lang="fr">
<head>
<meta charset="utf-8">
<title>Claireval Conseil et Comptes SA — Carte de visite</title>
<link href="https://fonts.googleapis.com/css2?family=Montserrat:wght@400;600;700&family=Open+Sans:wght@400;600&display=swap" rel="stylesheet">
<style>
  :root {
    --bg: #e9ecef;
    --paper: #ffffff;
    --ink: #333a40;
    --ink-soft: #4a5057;
    --brand: #1e88cc;
    --brand-dark: #17629c;
    --brand-light: #35b0e3;
    --rule: #c9ced3;
  }
  * { box-sizing: border-box; margin: 0; padding: 0; }
  html, body { width: 1200px; height: 823px; overflow: hidden; }
  body {
    background: var(--bg);
    display: flex;
    align-items: center;
    justify-content: center;
    gap: 70px;
    font-family: "Open Sans", Arial, sans-serif;
  }
  .card {
    width: 380px;
    height: 620px;
    border-radius: 22px;
    box-shadow: 0 14px 30px rgba(0,0,0,.18);
    overflow: hidden;
  }
  .card-front {
    background: var(--paper);
    display: flex;
    flex-direction: column;
    align-items: center;
    padding: 100px 30px 0;
    text-align: center;
    color: var(--ink);
  }
  .wordmark { display: flex; align-items: center; gap: 12px; }
  .wordmark-square { width: 26px; height: 26px; background: var(--brand); }
  .wordmark-name {
    font-family: "Montserrat", Arial, sans-serif;
    font-weight: 700;
    font-size: 36px;
    letter-spacing: 3px;
    color: var(--ink);
  }
  .wordmark-tagline {
    font-family: "Montserrat", Arial, sans-serif;
    font-weight: 400;
    font-size: 12px;
    letter-spacing: 4px;
    text-transform: uppercase;
    color: var(--ink-soft);
    margin-top: 8px;
  }
  .holder-name {
    margin-top: 58px;
    font-family: "Montserrat", Arial, sans-serif;
    font-weight: 700;
    font-size: 25px;
    text-transform: uppercase;
    color: var(--brand);
    letter-spacing: -0.5px;
  }
  .holder-role { font-size: 16px; line-height: 1.35; margin-top: 6px; }
  .rule { width: 220px; height: 1px; background: var(--rule); margin: 16px 0; }
  .icon-row { display: flex; gap: 6px; margin-bottom: 10px; }
  .icon { width: 24px; height: 24px; border-radius: 50%; display: flex; align-items: center; justify-content: center; }
  .icon-phone { background: var(--brand-dark); }
  .icon-mail { background: var(--brand); }
  .icon-web { background: var(--brand-light); }
  .contact-list, .address { list-style: none; font-size: 16px; line-height: 1.4; }
  .card-back {
    background: linear-gradient(20deg, var(--brand-dark) 0%, var(--brand) 50%, var(--brand-light) 100%);
    display: flex;
    flex-direction: column;
    align-items: center;
    justify-content: center;
    color: var(--paper);
  }
  .card-back .wordmark-square { background: var(--paper); }
  .card-back .wordmark-name, .card-back .wordmark-tagline { color: var(--paper); }
</style>
</head>
<body>
  <section class="card card-front" aria-label="Recto de la carte">
    <div class="wordmark">
      <span class="wordmark-square"></span>
      <span class="wordmark-name">CLAIREVAL</span>
    </div>
    <p class="wordmark-tagline">Conseil et Comptes</p>

    <h1 class="holder-name">Tomas Varenholt</h1>
    <p class="holder-role">Directeur et Fondateur<br>Expert-comptable diplômé</p>

    <div class="rule"></div>

    <div class="icon-row">
      <span class="icon icon-phone"><svg width="12" height="12" viewBox="0 0 24 24"><path fill="#fff" d="M6.6 10.8a15 15 0 0 0 6.6 6.6l2.2-2.2a1 1 0 0 1 1-.25 11.4 11.4 0 0 0 3.6.57 1 1 0 0 1 1 1V20a1 1 0 0 1-1 1A17 17 0 0 1 3 4a1 1 0 0 1 1-1h3.5a1 1 0 0 1 1 1c0 1.25.2 2.45.57 3.57a1 1 0 0 1-.25 1z"/></svg></span>
      <span class="icon icon-mail"><svg width="12" height="12" viewBox="0 0 24 24"><path fill="#fff" d="M2 5h20v14H2z"/><path fill="none" stroke="#1e88cc" stroke-width="2" d="M2 6l10 7 10-7"/></svg></span>
      <span class="icon icon-web"><svg width="12" height="12" viewBox="0 0 24 24" fill="none" stroke="#fff" stroke-width="2"><circle cx="12" cy="12" r="9"/><path d="M3 12h18M12 3c3 3 3 15 0 18M12 3c-3 3-3 15 0 18"/></svg></span>
    </div>

    <ul class="contact-list">
      <li>022 418 57 34</li>
      <li>tv@clairevalconseil.ch</li>
      <li>www.clairevalconseil.ch</li>
    </ul>

    <div class="rule"></div>

    <ul class="address">
      <li>Claireval Conseil et Comptes SA</li>
      <li>Rue des Vergières 27</li>
      <li>1201 Genève</li>
    </ul>
  </section>

  <section class="card card-back" role="img" aria-label="Verso de la carte : dégradé bleu avec le nom Claireval Conseil et Comptes">
    <div class="wordmark">
      <span class="wordmark-square"></span>
      <span class="wordmark-name">CLAIREVAL</span>
    </div>
    <p class="wordmark-tagline">Conseil et Comptes</p>
  </section>
</body>
</html>
```